Stylish Business Cards Wanted

- DOUBLE SIDED Design Required -

High end, edgy cards for a corporate and personal stylist. Must include logo,
Name: Belinda Harwick
Title: Director and Stylist
telephone : +61 8 7142 5809
email: belinda@theloombriefing.example
website: theloombriefing.example
Tag: Corporate Workwear & Uniform Specialist | Personal Stylist
Would like nice icons for telephone, email, website

Target Market(s)

Businesses wanting stylish uniforms, people wanting stylish wardrobes

Industry/Entity Type

Corporate Workwear Stylist

Contact Information for Business Card

I would like black, white and gold foiling incorporated in the design - possibly a touch of the other colours on my branding guide attached Name: Belinda Harwick Title: Director and Stylist telephone : +61 8 7142 5809 email: belinda@theloombriefing.example website: theloombriefing.example Tag: Corporate Workwear & Uniform Specialist | Personal Stylist Would like nice icons for telephone, email, website

Font styles to use
Other font styles liked:
• Raleway

Colors

Designer to choose colors to be used in the design.

Requirements
Must have
• Gold foil accents

```html
<!DOCTYPE html>
<html lang="en">
<head>
<meta charset="utf-8">
<title>The Loom Briefing – Business Cards</title>
<link rel="stylesheet" href="https://fonts.googleapis.com/css2?family=Raleway:wght@700&family=Roboto:wght@400&family=Dancing+Script:wght@500&display=swap">
<style>
  :root {
    --backdrop: #c9c9c9;
    --navy: #151b33;
    --gold: #e0b84a;
    --white: #fdfdfb;
    --ink: #1c1c22;
    --pink: #e2177a;
  }
  * { box-sizing: border-box; margin: 0; padding: 0; }
  html, body { width: 1200px; height: 852px; overflow: hidden; }
  body {
    background: var(--backdrop);
    position: relative;
    font-family: "Roboto", Arial, sans-serif;
  }
  .card {
    position: absolute;
    width: 540px;
    height: 310px;
    border-radius: 22px;
    overflow: hidden;
    box-shadow: 0 6px 16px rgba(0,0,0,0.18);
  }
  .card--front { left: 45px; top: 271px; background: var(--navy); }
  .card--back  { left: 615px; top: 271px; background: var(--white); }

  .brand {
    font-family: "Raleway", Arial, sans-serif;
    font-weight: 700;
    letter-spacing: 0.04em;
    text-align: center;
    line-height: 1.05;
  }
  .card--front .brand {
    position: absolute; inset: 0;
    display: flex; align-items: center; justify-content: center;
    color: var(--gold);
    font-size: 44px;
  }
  .card--back .brand {
    position: absolute; right: 44px; top: 24px;
    color: var(--navy);
    font-size: 26px;
  }

  .backdrop-shapes { position: absolute; inset: 0; }

  .contact { position: absolute; left: 40px; top: 104px; }
  .contact__name {
    font-family: "Dancing Script", cursive;
    font-weight: 500;
    font-size: 31px;
    color: var(--gold);
    line-height: 1;
  }
  .contact__title { font-size: 13px; color: var(--ink); margin-top: 6px; }
  .contact__list { list-style: none; margin-top: 16px; }
  .contact__item {
    display: flex; align-items: center; gap: 10px;
    font-size: 13.5px; color: var(--ink);
    height: 22px;
  }
  .contact__item--social { margin-bottom: 6px; }
  .contact__icon { width: 14px; height: 14px; flex: none; }
  .contact__square { width: 12px; height: 12px; background: var(--gold); border-radius: 2px; flex: none; }

  .tagline {
    position: absolute; right: 20px; bottom: 58px;
    font-family: "Dancing Script", cursive;
    font-weight: 500;
    font-size: 13px;
    line-height: 1.3;
    color: var(--white);
    text-align: right;
  }
</style>
</head>
<body>

  <section class="card card--front" aria-label="Card front">
    <div class="brand">The Loom<br>Briefing</div>
  </section>

  <section class="card card--back" aria-label="Card back">
    <svg class="backdrop-shapes" width="540" height="310" viewBox="0 0 540 310" aria-hidden="true">
      <rect x="0" y="150" width="9" height="72" rx="4" fill="var(--pink)"/>
      <path d="M0 294 C100 296 200 294 240 292 C340 285 390 225 420 170 C450 115 495 100 540 96 L540 310 L0 310 Z" fill="var(--navy)"/>
      <path d="M0 285 C100 287 200 285 238 283 C330 275 380 215 410 160 C440 105 490 88 540 84" fill="none" stroke="var(--gold)" stroke-width="5"/>
      <path d="M262 272 C330 264 370 226 396 182" fill="none" stroke="var(--gold)" stroke-width="2"/>
    </svg>

    <div class="brand">The Loom<br>Briefing</div>

    <div class="contact">
      <p class="contact__name">Belinda Harwick</p>
      <p class="contact__title">Director and Stylist</p>
      <ul class="contact__list">
        <li class="contact__item contact__item--social"><span class="contact__square"></span>/theloombriefing101</li>
        <li class="contact__item">
          <svg class="contact__icon" viewBox="0 0 16 16" aria-hidden="true"><path d="M4 1.5 L6.5 4.5 L5 6.2 C6 8.3 7.7 10 9.8 11 L11.5 9.5 L14.5 12 L13 14.5 C7 14 2 9 1.5 3 Z" fill="none" stroke="var(--gold)" stroke-width="1.3" stroke-linejoin="round"/></svg>
          +61 8 7142 5809
        </li>
        <li class="contact__item">
          <svg class="contact__icon" viewBox="0 0 16 16" aria-hidden="true"><rect x="1.5" y="3.5" width="13" height="9" rx="1" fill="none" stroke="var(--gold)" stroke-width="1.3"/><path d="M1.5 4 L8 9 L14.5 4" fill="none" stroke="var(--gold)" stroke-width="1.3"/></svg>
          belinda@theloombriefing.example
        </li>
        <li class="contact__item">
          <svg class="contact__icon" viewBox="0 0 16 16" aria-hidden="true"><circle cx="8" cy="8" r="6.5" fill="none" stroke="var(--gold)" stroke-width="1.3"/><ellipse cx="8" cy="8" rx="2.8" ry="6.5" fill="none" stroke="var(--gold)" stroke-width="1.1"/><path d="M1.5 8 H14.5" stroke="var(--gold)" stroke-width="1.1"/></svg>
          theloombriefing.example
        </li>
      </ul>
    </div>

    <p class="tagline">Personal Stylist<br>Corporate Workwear<br>and Uniform Specialist</p>
  </section>

</body>
</html>
```